Luxury Business Card Design for High-End Window Treatments

Gilded Slatworks
Custom Plantation Shutters & Architectural Shading Systems

⸻

BACK

Daniel Trevick
Owner

Custom Interior & Exterior Window Treatments

919-555-0148
gildedslatworks.com

I have included a picture that I’m hoping we can use on the back, but I’m also wondering if you can get rid of the ladder? Should we get rid of shutters , shades and blinds underneath Gilded Slatworks?

Target Market(s)

High-end residential homeowners, custom home builders, architects, interior designers, and luxury renovation clients seeking premium plantation shutters and motorized architectural shading systems.

Industry/Entity Type

Custom Window treatments

Contact Information for Business Card

Front Gilded Slatworks Custom Plantation Shutters Motorized Architectural Shading Systems BACK Daniel Trevick Owner 919-555-0148 GildedSlatworks.com Custom Interior & Exterior Window Treatments By Appointment

Requirements
Nice to have
• Not 100% sure on nice to halves or the color but you can definitely check out my website to get a better understanding of what I’m trying to do

```html
<!DOCTYPE html>
<html lang="en">
<head>
<meta charset="utf-8">
<title>Gilded Slatworks – Business Card</title>
<link rel="stylesheet" href="https://fonts.googleapis.com/css2?family=Merriweather:wght@400;700&family=Raleway:wght@400&display=swap">
<style>
  :root {
    --stage: #3a3a3d;
    --card: #232226;
    --gold: #c49a36;
    --white: #f4f2ee;
    --ring: #303034;
    --sky: #8fb4e0;
    --siding: #3b4150;
    --foliage: #4d5a33;
  }
  * { box-sizing: border-box; margin: 0; padding: 0; }
  html, body { width: 1200px; height: 758px; overflow: hidden; }
  body {
    background: var(--stage);
    display: flex;
    align-items: center;
    justify-content: center;
    gap: 40px;
    font-family: "Merriweather", Georgia, serif;
  }
  .card {
    position: relative;
    width: 540px;
    height: 309px;
    border-radius: 18px;
    background: var(--card);
    overflow: hidden;
    box-shadow: 0 14px 30px rgba(0,0,0,.45);
  }

  /* Front */
  .card--front {
    display: flex;
    flex-direction: column;
    align-items: center;
    justify-content: center;
    gap: 18px;
  }
  .brand-name {
    color: var(--gold);
    font-weight: 400;
    font-size: 44px;
    line-height: 1.05;
    text-align: center;
    letter-spacing: .5px;
  }
  .product-line {
    display: flex;
    gap: 28px;
    color: var(--gold);
    font-weight: 700;
    font-size: 22px;
    letter-spacing: .5px;
  }

  /* Back */
  .photo-art { position: absolute; inset: 0; }
  .back-content {
    position: absolute;
    left: 30px;
    top: 36px;
    width: 240px;
  }
  .back-brand {
    color: var(--gold);
    font-weight: 400;
    font-size: 27px;
    line-height: 1.1;
    margin-bottom: 22px;
  }
  .person {
    position: relative;
    padding-left: 20px;
  }
  .person::before {
    content: "";
    position: absolute;
    left: 0; top: 6px;
    width: 8px; height: 40px;
    background: var(--gold);
  }
  .person-name {
    color: var(--white);
    font-weight: 400;
    font-size: 19px;
    text-transform: uppercase;
    letter-spacing: .5px;
    white-space: nowrap;
  }
  .person-role {
    color: var(--gold);
    font-family: "Raleway", Arial, sans-serif;
    font-size: 15px;
    margin-top: 2px;
  }
  .services {
    color: var(--gold);
    font-weight: 700;
    font-size: 13px;
    line-height: 1.4;
    margin: 14px 0 12px 20px;
    white-space: nowrap;
  }
  .contact-list { list-style: none; margin-left: 20px; }
  .contact-item {
    display: flex;
    align-items: center;
    gap: 8px;
    color: var(--white);
    font-size: 14px;
    line-height: 1.6;
  }
  .contact-icon { width: 16px; height: 16px; flex: none; }
</style>
</head>
<body>

  <section class="card card--front">
    <h1 class="brand-name">Gilded<br>Slatworks</h1>
    <p class="product-line"><span>Shutters</span><span>Shades</span><span>Blinds</span></p>
  </section>

  <section class="card card--back">
    <svg class="photo-art" width="540" height="309" viewBox="0 0 540 309">
      <defs>
        <linearGradient id="house-tones" x1="0" y1="0" x2="0" y2="1">
          <stop offset="0" stop-color="var(--sky)"/>
          <stop offset=".35" stop-color="var(--siding)"/>
          <stop offset=".7" stop-color="#6e6a5e"/>
          <stop offset="1" stop-color="var(--foliage)"/>
        </linearGradient>
      </defs>
      <circle cx="452" cy="70" r="200" fill="var(--gold)"/>
      <circle cx="464" cy="58" r="192" fill="var(--ring)"/>
      <circle cx="478" cy="50" r="182" fill="url(#house-tones)" role="img" aria-label="Photo of a two-storey home with a covered porch, white columns, screened windows and Adirondack chairs on the lawn"/>
    </svg>

    <div class="back-content">
      <h2 class="back-brand">Gilded<br>Slatworks</h2>
      <div class="person">
        <p class="person-name">Daniel Trevick</p>
        <p class="person-role">Owner</p>
      </div>
      <p class="services">Custom Interior &amp; Exterior<br>Window Treatments</p>
      <ul class="contact-list">
        <li class="contact-item">
          <svg class="contact-icon" viewBox="0 0 16 16" aria-hidden="true">
            <circle cx="8" cy="8" r="8" fill="var(--gold)"/>
            <path d="M5 4.5c.6-.4 1.2-.3 1.5.2l.6 1.2c.2.4 0 .8-.3 1l-.4.3c.4 1 1.1 1.7 2 2.1l.3-.4c.3-.3.7-.4 1-.2l1.2.6c.5.3.6.9.2 1.5-.6.8-1.6 1-2.6.5C6.8 10.5 5.5 9.2 4.8 7.5c-.4-1-.3-2.3.2-3z" fill="var(--card)"/>
          </svg>
          919-555-0148
        </li>
        <li class="contact-item">
          <svg class="contact-icon" viewBox="0 0 16 16" aria-hidden="true">
            <circle cx="8" cy="8" r="8" fill="var(--gold)"/>
            <g fill="none" stroke="var(--card)" stroke-width="1">
              <circle cx="8" cy="8" r="4.5"/>
              <ellipse cx="8" cy="8" rx="2" ry="4.5"/>
              <line x1="3.5" y1="8" x2="12.5" y2="8"/>
            </g>
          </svg>
          gildedslatworks.com
        </li>
      </ul>
    </div>
  </section>

</body>
</html>
```